full stationary design for a modern sleek design company

we are a design company that does modern minimalistic interior design works as well as other design services for high end clients.
we need a full stationary design including and not limited to (double sided business card, letter head, envelopes, documents folder...etc) that reflects the modern style design we do.
sleek modern and minimalistic is the requirements.
Updates

please use the latest attached files as there was a slight modification on the logo Added Wednesday, March 1, 2017

minor update on the logo files in JPG and PSD has been updated kindly follow the new attachments. Added Thursday, March 2, 2017

Target Market(s)

modern minimalist clients

Industry/Entity Type

Design Agency

Requirements
Must have
• the logo
Nice to have
• i like the colors in the colored 3D logo attached
Should not have
• too many colors

```html
<!DOCTYPE html>
<html lang="en">
<head>
<meta charset="utf-8">
<title>Linea Atelier – Business Card</title>
<link rel="stylesheet" href="https://fonts.googleapis.com/css2?family=Source+Sans+3:wght@400;600&display=swap">
<style>
  :root {
    --backdrop: #3b3b3b;
    --card-white: #f7f7f7;
    --ink: #2b2b2b;
    --accent: #ef8a1c;
    --on-dark: #ffffff;
  }
  html, body {
    margin: 0;
    padding: 0;
    width: 1200px;
    height: 750px;
    overflow: hidden;
    background: var(--backdrop);
    font-family: "Source Sans 3", "Myriad Pro", sans-serif;
  }
  .canvas {
    position: relative;
    width: 1200px;
    height: 750px;
  }
  .card {
    position: absolute;
    top: 228px;
    width: 461px;
    height: 262px;
    border-radius: 14px;
    overflow: hidden;
  }
  .card--front { left: 124px; background: var(--card-white); }
  .card--back  { left: 618px; background: var(--accent); }

  .card__wave {
    position: absolute;
    inset: 0;
    width: 461px;
    height: 262px;
  }
  .wave-accent { fill: var(--accent); }
  .wave-dark { fill: var(--ink); stroke: var(--card-white); stroke-width: 3; }

  .brand {
    position: absolute;
    display: flex;
    align-items: center;
    gap: 9px;
    color: var(--ink);
    font-weight: 600;
  }
  .brand__mark {
    width: 30px;
    height: 30px;
    background: var(--accent);
  }
  .card--back .brand__mark { background: var(--ink); }
  .brand__words { display: flex; flex-direction: column; line-height: 1; }
  .brand__name {
    font-size: 25px;
    letter-spacing: 1.5px;
    text-transform: uppercase;
  }
  .brand__tagline {
    margin-top: 3px;
    font-size: 10px;
    letter-spacing: 6.4px;
    text-transform: uppercase;
  }
  .card--front .brand { left: 34px; top: 34px; }
  .card--back .brand { left: 50%; top: 50%; transform: translate(-50%, -50%); }

  .person {
    position: absolute;
    left: 34px;
    top: 148px;
  }
  .person__name {
    margin: 0;
    font-size: 17.5px;
    font-weight: 600;
    color: var(--accent);
    line-height: 1.1;
    text-transform: uppercase;
  }
  .person__role {
    margin: 1px 0 0;
    font-size: 13px;
    color: var(--ink);
  }

  .contact {
    position: absolute;
    right: 35px;
    top: 127px;
    margin: 0;
    padding: 0;
    list-style: none;
    color: var(--on-dark);
    font-size: 12.5px;
    text-align: right;
    line-height: 17px;
  }
  .contact__address { margin-bottom: 7px; }
  .contact__item {
    display: flex;
    justify-content: flex-end;
    align-items: center;
    gap: 6px;
    height: 17.5px;
  }
  .contact__icon { width: 11px; height: 11px; flex: none; }
  .contact__icon * { fill: none; stroke: var(--accent); stroke-width: 1.6; }
  .contact__icon .solid { fill: var(--accent); stroke: none; }
</style>
</head>
<body>
<main class="canvas">

  <section class="card card--front" aria-label="Business card front">
    <svg class="card__wave" viewBox="0 0 461 262" aria-hidden="true">
      <path class="wave-accent" d="M0,182 C40,206 110,214 170,190 C215,172 255,140 285,118 C250,150 215,186 170,206 C110,230 40,222 0,204 Z"/>
      <path class="wave-dark" d="M0,204 C40,224 110,230 172,206 C250,176 320,92 380,64 C415,50 445,58 463,72 V264 H-2 Z"/>
    </svg>

    <div class="brand">
      <span class="brand__mark"></span>
      <span class="brand__words">
        <span class="brand__name">Linea Atelier</span>
        <span class="brand__tagline">by Marc Veyron</span>
      </span>
    </div>

    <div class="person">
      <h1 class="person__name">Adam Carter</h1>
      <p class="person__role">CEO&amp;Founder</p>
    </div>

    <ul class="contact">
      <li class="contact__address">2140 Birchwood Road<br>Portland, Oregon 97201</li>
      <li class="contact__item">(555) 201 4480
        <svg class="contact__icon" viewBox="0 0 12 12" aria-hidden="true"><path class="solid" d="M2.2,0.8 L4.2,0.8 L5,3.4 L3.6,4.6 C4.3,6 5.8,7.6 7.3,8.3 L8.5,6.9 L11.1,7.8 L11.1,9.8 C11.1,10.6 10.4,11.2 9.6,11.1 C5,10.5 1.3,6.8 0.8,2.3 C0.7,1.5 1.3,0.8 2.2,0.8 Z"/></svg>
      </li>
      <li class="contact__item">(555) 317 9026
        <svg class="contact__icon" viewBox="0 0 12 12" aria-hidden="true"><rect x="2.8" y="0.8" width="6.4" height="10.4" rx="1"/></svg>
      </li>
      <li class="contact__item">adam@lineaatelier.com
        <svg class="contact__icon" viewBox="0 0 12 12" aria-hidden="true"><rect class="solid" x="0.5" y="2.5" width="11" height="7.5"/><path style="stroke:var(--ink);stroke-width:1" d="M0.8,2.8 L6,6.8 L11.2,2.8"/></svg>
      </li>
      <li class="contact__item">www.lineaatelier.com
        <svg class="contact__icon" viewBox="0 0 12 12" aria-hidden="true"><circle class="solid" cx="6" cy="6" r="5.5"/><path style="stroke:var(--ink);stroke-width:1" d="M0.8,6 H11.2 M6,0.6 C3.6,3.5 3.6,8.5 6,11.4 M6,0.6 C8.4,3.5 8.4,8.5 6,11.4"/></svg>
      </li>
    </ul>
  </section>

  <section class="card card--back" aria-label="Business card back">
    <div class="brand">
      <span class="brand__mark"></span>
      <span class="brand__words">
        <span class="brand__name">Linea Atelier</span>
        <span class="brand__tagline">by Marc Veyron</span>
      </span>
    </div>
  </section>

</main>
</body>
</html>
```